Website Design for The Elder Nook

Please design and code a new website.
Here are the sites I like best:
http://www.voyaglint.com/alternate/
http://www.wheelgiftbay.org
Please make it similar but look at the competitor site (below) for images and wording. This is NOT a car donation site. It's a senior lead placement site like https://www.kinhavenfinder.com. I just like this sites above as a lead generation sites.
Competitor site:
https://www.kinhavenfinder.com (use ideas / verbiage from this site)
Updates
Competitor site:
Coding
Coded - Design and coding required
Number of Pages Required
1 page
Look and feel
Each slider illustrates characteristics of the customer's brand and the style your logo design should communicate.

```html
<!DOCTYPE html>
<html lang="en">
<head>
<meta charset="utf-8">
<title>The Elder Nook — Senior Living Advice</title>
<link rel="stylesheet" href="https://fonts.googleapis.com/css2?family=Libre+Baskerville:ital,wght@0,400;1,400&family=Jost:wght@300;400;500&display=swap">
<style>
:root{
  --blue:#0f5bb0;
  --blue-dark:#0b4f9c;
  --green:#8cc63f;
  --ink:#2b2b2b;
  --muted:#666;
  --line:#e3e3e3;
  --white:#fff;
}
*{box-sizing:border-box;margin:0;padding:0}
html,body{width:1200px;height:2984px;overflow:hidden}
body{font-family:"Jost",sans-serif;color:var(--ink);background:var(--white);position:relative}
.serif{font-family:"Libre Baskerville",serif}
.abs{position:absolute}
.center{text-align:center}
.green{color:var(--green)}
.blue{color:var(--blue)}

/* header */
.header{position:absolute;top:0;left:0;width:1200px;height:90px}
.brand{position:absolute;left:140px;top:30px;display:flex;align-items:center;gap:8px;font-family:"Libre Baskerville",serif;font-size:22px;color:var(--green)}
.brand i{width:16px;height:16px;border-radius:50%;background:var(--green);display:block}
.call{position:absolute;left:714px;top:22px;display:flex;gap:12px;align-items:center}
.call small{display:block;font-family:"Libre Baskerville",serif;font-size:10px;color:#444}
.call strong{display:block;font-weight:400;font-size:24px;color:var(--blue);line-height:1.1}
.lang{position:absolute;left:957px;top:28px;width:102px;height:34px;background:var(--green);color:#fff;font-size:12px;display:flex;align-items:center;gap:8px;padding-left:14px}
.lang span.flag{width:32px;height:18px;background:linear-gradient(#c9343a 0 50%,#f3f3f3 50%);display:block}

/* nav */
.nav{position:absolute;top:90px;left:0;width:1200px;height:43px;background:var(--blue)}
.nav ul{list-style:none;display:flex;position:absolute;left:140px;top:0;height:43px}
.nav li{font-family:"Libre Baskerville",serif;font-size:12px;color:#fff;padding:0 11px;line-height:43px;border-right:1px solid rgba(255,255,255,.25)}
.nav li.active{background:var(--blue-dark);border-bottom:3px solid var(--green)}

/* hero */
.hero{position:absolute;top:133px;left:0;width:1200px;height:517px;background:linear-gradient(90deg,#d9dcc8 0%,#e9e6d6 45%,#b9c69a 60%,#7fa0b7 75%,#c9cfa9 100%)}
.hero-panel{position:absolute;left:0;top:0;width:600px;height:517px;background:rgba(255,255,255,.45)}
.hero h1{position:absolute;top:75px;left:0;width:740px;font-weight:400;font-size:32px;line-height:42px;color:#333}
.hero h1 em{color:var(--blue)}
.hero .lead{position:absolute;top:168px;left:0;width:740px;font-size:19px;font-weight:300}
.field{background:#fff;border:1px solid #ccc;font-size:14px;color:#444;display:flex;align-items:center;padding-left:20px}
.btn{background:var(--green);color:#fff;font-family:"Libre Baskerville",serif;display:flex;align-items:center;justify-content:center}
.badge{position:absolute;left:288px;top:378px;width:156px;height:58px;border:2px solid var(--blue);border-radius:6px;background:var(--blue)}

/* support */
h2{font-family:"Libre Baskerville",serif;font-weight:400;font-size:28px}
.intro{font-size:14px;line-height:24px;color:#333}
.card{position:absolute;top:843px;width:172px;height:180px;border:1px solid var(--line);box-shadow:0 2px 6px rgba(0,0,0,.08);text-align:center;font-size:17px;line-height:21px;padding:0 8px}
.card svg{display:block;margin:24px auto 8px}

/* advisors */
.advisors{position:absolute;top:1195px;left:0;width:1200px;height:480px;background:linear-gradient(90deg,#1b5aa6,#2a6ab3 30%,#1f5fab 60%,#2b6cb4 85%,#1a58a4)}
.advisors .ring{position:absolute;top:175px;width:96px;height:96px;border:1.5px solid #fff;border-radius:50%;display:flex;align-items:center;justify-content:center}
.advisors .label{position:absolute;top:283px;width:200px;color:#fff;font-size:16px;line-height:20px;text-align:center;font-weight:300}

/* testimonials */
.quote{position:absolute;top:1813px;width:285px;height:147px;border:1px solid var(--line);padding:20px 18px;font-size:13px;line-height:22px;color:#777;letter-spacing:.3px}
.avatar{position:absolute;top:1940px;width:70px;height:70px;border-radius:50%;border:3px solid var(--blue);background:linear-gradient(#e6d6c4,#b89a7e)}
.person{position:absolute;top:1977px;font-family:"Libre Baskerville",serif;font-size:14px}

/* veterans */
.veterans{position:absolute;top:2158px;left:0;width:1200px;height:293px;background:linear-gradient(160deg,#1d2230 0%,#3a2a33 40%,#2b2a31 60%,#151619 100%);color:#fff}

/* states */
.states{position:absolute;top:2590px;font-size:13px;line-height:22px;color:#333;list-style:none}
.states li::before{content:"› "}

/* footer */
.footer{position:absolute;top:2812px;left:0;width:1200px;height:172px;background:var(--blue);color:#fff}
.footer ul{list-style:none;display:flex;justify-content:center;gap:34px;position:absolute;top:50px;width:1200px;font-family:"Libre Baskerville",serif;font-size:11px}
.footer hr{position:absolute;top:115px;left:140px;width:918px;border:0;border-top:1px solid rgba(255,255,255,.25)}
.social{position:absolute;top:132px;display:flex;gap:6px;left:945px}
.social i{width:24px;height:24px;border-radius:50%;border:1.5px solid #fff;background:#3c79c0;display:block}
</style>
</head>
<body>

<header class="header">
  <div class="brand"><i></i>The Elder Nook</div>
  <div class="call">
    <svg width="34" height="34" viewBox="0 0 24 24" fill="none" stroke="#0f5bb0" stroke-width="1.4"><path d="M5 3h4l2 5-2.5 1.5a11 11 0 0 0 6 6L16 13l5 2v4a2 2 0 0 1-2 2A17 17 0 0 1 3 5a2 2 0 0 1 2-2z"/></svg>
    <div><small>Talk to a local advisor for FREE</small><strong>(123) 456-7890</strong></div>
  </div>
  <div class="lang">En <span class="flag"></span>⌄</div>
</header>

<nav class="nav">
  <ul>
    <li class="active">ASSISTED LIVING</li><li>MEMORY CARE</li><li>NURSING HOMES</li><li>MORE LIVING OPTIONS ⌄</li><li>PLANNING &amp; ADVICE</li><li>HOW OUR SERVICE WORKS</li>
  </ul>
</nav>

<section class="hero" role="img" aria-label="Photo of a smiling senior couple embracing outdoors in soft sunlight">
  <div class="hero-panel"></div>
  <h1 class="serif center">You know your family.<br>We know <em>Senior Living.</em></h1>
  <p class="lead center">Find Senior Living Near You.</p>
  <div class="field abs" style="left:175px;top:207px;width:392px;height:46px">Enter city or postal code</div>
  <div class="btn abs" style="left:175px;top:262px;width:392px;height:48px;font-size:16px">Start Your Search</div>
  <p class="abs center" style="left:0;top:336px;width:740px;font-size:19px;font-weight:300">Need help? Call (123) 456-7890</p>
  <div class="badge"></div>
  <p class="abs center" style="left:288px;top:440px;width:156px;font-size:12px;font-weight:500;color:var(--blue)">Rated A+</p>
</section>

<h2 class="abs center" style="top:727px;left:0;width:1200px"><span class="green">The Support You Need To</span> <span class="blue">Make The Right Choice</span></h2>
<p class="intro abs center" style="top:773px;left:200px;width:800px">Lorem ipsum dolor sit amet, consectetuer adipiscing elit, sed diam nonummy nibh euismod tincidunt ut laoreet dolore magna aliquam erat volutpat. Ut wisi enim ad minim veniam, quis nostrud exerci tation ullamcorper suscipit.</p>

<div class="card" style="left:140px"><svg width="50" height="56" viewBox="0 0 50 56" fill="none" stroke="#8cc63f" stroke-width="1.6"><circle cx="25" cy="14" r="9"/><path d="M6 54V40a10 10 0 0 1 10-10h18a10 10 0 0 1 10 10v14M25 30l-3 24h6z"/></svg>Dedicated local advisor</div>
<div class="card" style="left:327px"><svg width="50" height="56" viewBox="0 0 50 56" fill="none" stroke="#8cc63f" stroke-width="1.6"><path d="M3 26 25 4l22 22M9 20v34h32V20M20 54V38h10v16"/></svg>Hand-picked list of communities to match your needs</div>
<div class="card" style="left:514px"><svg width="50" height="56" viewBox="0 0 50 56" fill="none" stroke="#8cc63f" stroke-width="1.6"><circle cx="25" cy="20" r="10"/><path d="M25 14v12M22 17h5M22 23h5M4 44h10l10 4 20-8M25 2v4M33 5l-2 3M17 5l2 3"/></svg>Full details and pricing</div>
<div class="card" style="left:700px"><svg width="52" height="56" viewBox="0 0 52 56" fill="none" stroke="#8cc63f" stroke-width="1.6"><rect x="2" y="6" width="48" height="46"/><path d="M2 16h48M12 2v8M40 2v8M12 24h28v20H12zM19 24v20M26 24v20M33 24v20M12 31h28M12 38h28"/></svg>Help scheduling tours</div>
<div class="card" style="left:887px"><svg width="62" height="56" viewBox="0 0 62 56" fill="none" stroke="#8cc63f" stroke-width="1.6"><path d="M10 10h30v30H10zM40 20h10l8 10v10H40M2 18h12M4 26h10M6 34h8"/><circle cx="18" cy="44" r="5"/><circle cx="48" cy="44" r="5"/></svg>Move in support</div>

<h2 class="abs" style="top:1080px;left:140px;font-size:24px"><span class="green">There's</span> <span class="blue">No Cost To You.</span></h2>
<p class="abs" style="top:1068px;left:426px;font-size:17px;line-height:25px;font-weight:300">We work with over 20,000 senior living communities.<br>Our community partners pay us for placement services.</p>
<p class="abs blue" style="top:1080px;left:869px;font-size:20px;font-weight:300">Call (123) 456-7890</p>

<section class="advisors" role="img" aria-label="Row of portrait photos of smiling local advisors under a blue tint">
  <h2 class="abs center" style="top:78px;left:0;width:1200px;color:#fff">Your local advisor informs. You decide.</h2>
  <p class="abs center" style="top:126px;left:0;width:1200px;color:#fff;font-size:14px;font-weight:300">Lorem ipsum dolor sit amet, consectetuer adipiscing elit, sed diam nonummy nibh euismod tincidunt ut laoreet.</p>
  <div class="ring" style="left:291px"><svg width="34" height="60" viewBox="0 0 34 60" fill="none" stroke="#fff" stroke-width="1.8"><circle cx="17" cy="14" r="11"/><path d="M17 25v32"/></svg></div>
  <div class="ring" style="left:552px"><svg width="56" height="50" viewBox="0 0 56 50" fill="none" stroke="#fff" stroke-width="1.8"><path d="M28 46 6 24A12 12 0 0 1 28 8a12 12 0 0 1 22 16z"/></svg></div>
  <div class="ring" style="left:812px"><svg width="52" height="44" viewBox="0 0 52 44" fill="none" stroke="#fff" stroke-width="1.8"><circle cx="5" cy="6" r="4"/><circle cx="5" cy="22" r="4"/><circle cx="5" cy="38" r="4"/><path d="M16 6h34M16 22h34M16 38h34"/></svg></div>
  <p class="label" style="left:239px">Insider's tips for the area near you</p>
  <p class="label" style="left:500px">Advice tailored to your unique situation</p>
  <p class="label" style="left:760px">Time saving know-how and resources</p>
  <div class="field abs" style="left:298px;top:351px;width:602px;height:44px;border:0">Enter city or postal code</div>
  <div class="btn abs" style="left:676px;top:355px;width:220px;height:36px;font-size:14px">Find an advisor near you</div>
</section>

<h2 class="abs center" style="top:1755px;left:0;width:1200px"><span class="green">93% Of Our Customers</span> <span class="blue">Recommend Our Service</span></h2>

<div class="quote" style="left:140px">Lorem ipsum dolor sit amet, consectetuer adipiscing elit, sed diam nonummy nibh euismod tincidunt ut laoreet dolore magna aliquam erat volutpat. Ut wisi enim ad minim veniam, quis nostrud.</div>
<div class="quote" style="left:457px">Lorem ipsum dolor sit amet, consectetuer adipiscing elit, sed diam nonummy nibh euismod tincidunt ut laoreet dolore magna aliquam erat volutpat. Ut wisi enim ad minim veniam, quis nostrud.</div>
<div class="quote" style="left:774px">Lorem ipsum dolor sit amet, consectetuer adipiscing elit, sed diam nonummy nibh euismod tincidunt ut laoreet dolore magna aliquam erat volutpat. Ut wisi enim ad minim veniam, quis nostrud.</div>
<div class="avatar" role="img" aria-label="Portrait photo of Mara Quill" style="left:151px"></div>
<div class="avatar" role="img" aria-label="Portrait photo of Owen Hartley" style="left:468px;background:linear-gradient(#dcc7b3,#3b4250)"></div>
<div class="avatar" role="img" aria-label="Portrait photo of Jenna Rowe" style="left:785px;background:linear-gradient(#d8b98c,#a77c55)"></div>
<p class="person" style="left:242px">Mara Quill</p>
<p class="person" style="left:559px">Owen Hartley</p>
<p class="person" style="left:876px">Jenna Rowe</p>
<div class="btn abs" style="left:496px;top:2036px;width:208px;height:38px;font-size:14px">See More Testimonials</div>

<section class="veterans" role="img" aria-label="Waving American flag in dark tones">
  <h2 class="abs center" style="top:72px;left:0;width:1200px;font-size:24px">Access Up To $2,000 Per Month In Veteran's Aid</h2>
  <p class="abs center" style="top:112px;left:0;width:1200px;font-size:14px;line-height:24px;font-weight:300">We work with Veterans every day. Most veteran families do not know of a key benefit available to them and their families.<br>It's called the Veteran's Aid and Attendance benefit. This benefit can help pay for senior living and home care.</p>
  <div class="btn abs" style="left:535px;top:177px;width:130px;height:38px;font-size:14px">Learn More</div>
</section>

<h2 class="abs center" style="top:2530px;left:0;width:1200px"><span class="green">Senior Assisted</span> <span class="blue">Living by State</span></h2>
<ul class="states" style="left:158px"><li>Alabama</li><li>Arizona</li><li>Arkansas</li><li>California</li><li>Colorado</li><li>Connecticut</li><li>Delaware</li></ul>
<ul class="states" style="left:301px"><li>District of Columbia</li><li>Florida</li><li>Georgia</li><li>Hawaii</li><li>Idaho</li><li>Illinois</li><li>Indiana</li></ul>
<ul class="states" style="left:486px"><li>Iowa</li><li>Kansas</li><li>Kentucky</li><li>Louisiana</li><li>Maine</li><li>Maryland</li><li>Massachusetts</li></ul>
<ul class="states" style="left:644px"><li>Michigan</li><li>Minnesota</li><li>Mississippi</li><li>Missouri</li><li>Montana</li><li>Nebraska</li><li>Nevada</li></ul>
<ul class="states" style="left:780px"><li>New Hampshire</li><li>New Jersey</li><li>New Mexico</li><li>New York</li><li>North Carolina</li><li>North Dakota</li><li>Ohio</li></ul>
<ul class="states" style="left:948px"><li>Oklahoma</li><li>Oregon</li><li>Pennsylvania</li><li>Rhode Island</li><li>South Carolina</li><li>South Dakota</li><li>Tennessee</li></ul>

<footer class="footer">
  <ul><li>ASSISTED LIVING</li><li>MEMORY CARE</li><li>NURSING HOMES</li><li>MORE LIVING OPTIONS ⌄</li><li>PLANNING &amp; ADVICE</li><li>HOW OUR SERVICE WORKS</li></ul>
  <hr>
  <p class="abs" style="left:140px;top:136px;font-size:13px;font-weight:300">Copyright 2019 The Elder Nook. All Rights Reserved.</p>
  <div class="social"><i></i><i></i><i></i><i></i></div>
</footer>

</body>
</html>
```